Business Card Design

We like to use greens as you will see in our logo (but not TOO much green). We are a Dental Clinic in a somewhat eccentric community. We do not like the dated sharp designs which we see many dentists use. We're looking for something bright and fresh while still maintaining the integrity of the profession. Elegance is not necessarily what we are going for... we need for the design to be "mature" but also up-lifting.

See our logo.
Updates

Project Deadline Extended
Reason: We have 5 designs which we like. But we'd like to see a few more before committing to a design.

Project Deadline Extended
Reason: We are awaiting revisions to this project. We are still welcoming designs while we wait to see if designers are able to provide to us the revisions we require in order to proceed with a selection.

Target Market(s)

Younger families - ages late 20's to early 40's

Industry/Entity Type

Business

Contact Information for Business Card

Corwel T. Banfry DDS 2730 W. Halvert Rd. Ste. 7 Larkmoor, ZN 48391 (555)555-0174 FX (555)555-0189 info@BrightwellDentalCareMi.com BrigthwellDentalCareMi.com on the back of the card we need an appointment reminder (For____ Date___ Time____) with "If you are unable to keep your appointment, kindly give 48 hours notice" at the bottom. No use of teeth in the design. DOUBLE SIDED DESIGN

Requirements
Should not have
• The use of pictures of teeth

```html
<!DOCTYPE html>
<html lang="en">
<head>
<meta charset="utf-8">
<title>Brightwell Dental Care – Business Card</title>
<link rel="stylesheet" href="https://fonts.googleapis.com/css2?family=Source+Sans+3:ital,wght@0,400;0,600;0,700;1,400&family=Cinzel:wght@600&display=swap">
<style>
  :root {
    --green: #1b6b35;
    --green-light: #8cc63f;
    --ink: #2b2b2b;
    --panel: #efefef;
    --paper: #ffffff;
    --backdrop: #e8e6e2;
    --rule: #4a4a4a;
  }
  * { box-sizing: border-box; margin: 0; padding: 0; }
  html, body { width: 1200px; height: 1177px; overflow: hidden; }
  body {
    position: relative;
    background: var(--backdrop);
    font-family: "Source Sans 3", "Myriad Pro", Arial, sans-serif;
    color: var(--ink);
  }
  .card {
    position: absolute;
    width: 916px; height: 524px;
    background: var(--paper);
    border: 1px solid #9a9a9a;
    overflow: hidden;
  }
  .card--front { left: 39px; top: 46px; }
  .card--back  { left: 248px; top: 608px; }

  /* front */
  .stripe { position: absolute; top: 0; bottom: 0; background: var(--green); }
  .stripe--thin { left: 62px; width: 12px; }
  .stripe--wide { left: 94px; width: 170px; }
  .stripe--edge { left: 886px; width: 30px; }

  .id-panel {
    position: absolute; left: 35px; top: 47px; width: 288px; height: 345px;
    background: var(--panel);
  }
  .brand {
    position: absolute; background: var(--paper);
    display: flex; flex-direction: column; align-items: center; justify-content: center;
    color: var(--green); font-weight: 600; text-align: center; line-height: 1.05;
  }
  .brand__dot { border-radius: 50%; background: var(--green-light); margin-bottom: 10px; }
  .card--front .brand { left: 7px; top: 12px; width: 272px; height: 215px; font-size: 36px; }
  .card--front .brand__dot { width: 54px; height: 54px; }
  .holder { position: absolute; left: 28px; top: 242px; }
  .holder__name { font-size: 31px; font-weight: 700; color: var(--green); line-height: 1.1; }
  .holder__title { font-size: 22px; margin-top: 8px; }

  .contact { position: absolute; left: 438px; top: 293px; font-size: 20px; }
  .contact__row { display: flex; height: 37.5px; align-items: center; }
  .contact__label { width: 82px; color: var(--green); font-weight: 600; }
  .contact__address { margin-top: 10px; line-height: 29px; }

  /* back */
  .card--back .brand { left: 72px; top: 11px; width: 217px; height: 132px; font-size: 28px; }
  .card--back .brand__dot { width: 40px; height: 40px; margin-bottom: 6px; }
  .appt-title {
    position: absolute; left: 77px; top: 168px;
    font-family: "Cinzel", "Trajan Pro", Georgia, serif;
    font-size: 33px; font-weight: 600; color: var(--green); letter-spacing: 1px;
  }
  .field { position: absolute; font-size: 27px; display: flex; align-items: baseline; white-space: nowrap; }
  .field__line { border-bottom: 2px dotted var(--rule); height: 1px; display: inline-block; }
  .field--name { left: 80px; top: 243px; }
  .field--name .field__line { width: 508px; margin-left: 30px; }
  .field--when { left: 80px; top: 308px; }
  .field--when .field__line--date { width: 164px; margin: 0 10px 0 36px; }
  .field--when .field__line--time { width: 153px; margin: 0 6px 0 9px; }
  .field--next { left: 80px; top: 373px; align-items: center; }
  .slot { width: 164px; height: 37px; border: 2px solid #555; border-radius: 5px; }
  .field--next .slot:first-of-type { margin-left: 39px; }
  .field--next .slot + .slot { margin-left: 39px; }

  .days { position: absolute; left: 755px; top: 77px; list-style: none; }
  .days__item { display: flex; align-items: center; height: 33px; font-size: 25px; font-weight: 600; }
  .days__item + .days__item { margin-top: 30px; }
  .days__item:nth-child(4) { margin-top: 32px; }
  .days__item:nth-child(5), .days__item:nth-child(6) { margin-top: 21px; }
  .days__label { width: 76px; }
  .days__box { width: 59px; height: 33px; border: 2px solid #555; border-radius: 5px; }

  .notice { position: absolute; left: 77px; top: 446px; font-size: 28px; font-style: italic; white-space: nowrap; }
  .footer-band { position: absolute; left: 0; right: 0; top: 508px; height: 11px; background: var(--green); }
</style>
</head>
<body>

<section class="card card--front" aria-label="Business card front">
  <div class="stripe stripe--thin"></div>
  <div class="stripe stripe--wide"></div>
  <div class="stripe stripe--edge"></div>

  <div class="id-panel">
    <div class="brand">
      <span class="brand__dot"></span>
      <span>Brightwell<br>Dental Care</span>
    </div>
    <div class="holder">
      <p class="holder__name">Corwel T. Banfry</p>
      <p class="holder__title">DDS</p>
    </div>
  </div>

  <div class="contact">
    <div class="contact__row"><span class="contact__label">Phone:</span><span>(555)555-0174</span></div>
    <div class="contact__row"><span class="contact__label">Fax:</span><span>(555)555-0189</span></div>
    <div class="contact__row"><span class="contact__label">Email:</span><span>info@BrightwellDentalCareMi.com</span></div>
    <div class="contact__row"><span class="contact__label">Web:</span><span>www.BrigthwellDentalCareMi.com</span></div>
    <p class="contact__address">2730 W. Halvert Rd. Ste. 7 Larkmoor<br>ZN 48391</p>
  </div>
</section>

<section class="card card--back" aria-label="Appointment card back">
  <div class="brand">
    <span class="brand__dot"></span>
    <span>Brightwell<br>Dental Care</span>
  </div>

  <h2 class="appt-title">YOUR APPOINTMENT</h2>

  <div class="field field--name">Name :<span class="field__line"></span></div>
  <div class="field field--when">Date :<span class="field__line field__line--date"></span>Time :<span class="field__line field__line--time"></span>am / pm</div>
  <div class="field field--next">Next Appointment<span class="slot"></span><span class="slot"></span></div>

  <ul class="days">
    <li class="days__item"><span class="days__label">MON</span><span class="days__box"></span></li>
    <li class="days__item"><span class="days__label">TUE</span><span class="days__box"></span></li>
    <li class="days__item"><span class="days__label">WED</span><span class="days__box"></span></li>
    <li class="days__item"><span class="days__label">THU</span><span class="days__box"></span></li>
    <li class="days__item"><span class="days__label">FRI</span><span class="days__box"></span></li>
    <li class="days__item"><span class="days__label">SAT</span><span class="days__box"></span></li>
  </ul>

  <p class="notice">If you are unable to keep your appointment, kindly give 48 hours notice</p>
  <div class="footer-band"></div>
</section>

</body>
</html>
```